7' x 4' sign for a new multiunit residential mountain location**

Our mission is to build people their dream home through the use of professional and thoughtful design. We're a new developer, building a new and feature-filled fourplex, and need a brand and presence that generates interests and builds our brand. Our homes are professionally and thoughtfully designed - we agonize over the details so our homeowners don't have to once they move in.

We're constructing a new fourplex in downtown Larchmere, Valley Coast. The location is in the heart of the city's entertainment and cultural zones, is surrounded by mountains and a lake, and within an hour of over 100 wineries. "Valley" residents prize their time outdoors - boating, biking, hiking, skiing, and more. It's no wonder Kelowna is often cited as one of the most beautiful and desirable places to live in the world.

attachments - brand elements, rendering of the unit, feature sheet for each unit, and picture of the sign casing (7' wide and 4' long envelop - pic of sign frame attached).

Target Market(s)

Young professionals (age 30 to 45); Empty nestes (age 55+)

Font styles to use
Other font styles liked:
• Cordia New

Requirements
Must have
• Our tag line - Living, with Intent

Presence - this is an unusual shape and large sign. It must create interest and build our brand.

```html
<!DOCTYPE html>
<html lang="en">
<head>
<meta charset="utf-8">
<title>217 Marlow – Living, with Intent</title>
<link rel="stylesheet" href="https://fonts.googleapis.com/css2?family=Libre+Caslon+Display&display=swap">
<style>
  :root {
    --page: #efeae2;
    --sign-face: #322a33;
    --sign-text: #aaa5a7;
    --peak-light: #f7f7f7;
    --peak-dark: #3a3139;
  }
  * { margin: 0; padding: 0; box-sizing: border-box; }
  html, body {
    width: 1200px;
    height: 667px;
    overflow: hidden;
    background: var(--page);
  }
  .canvas {
    position: relative;
    width: 1200px;
    height: 667px;
  }
  .mountain-crest {
    position: absolute;
    left: 408px;
    top: 69px;
    width: 363px;
    height: 67px;
    background: linear-gradient(180deg, var(--peak-light) 0%, var(--peak-light) 30%, var(--peak-dark) 100%);
    border-radius: 6px 6px 0 0;
  }
  .sign {
    position: absolute;
    left: 190px;
    top: 135px;
    width: 800px;
    height: 393px;
    background: var(--sign-face);
    color: var(--sign-text);
    font-family: "Libre Caslon Display", serif;
  }
  .sign__title {
    position: absolute;
    left: 0;
    top: 30px;
    width: 100%;
    text-align: center;
    font-weight: 400;
    font-size: 96px;
    line-height: 1;
    letter-spacing: 2px;
    white-space: nowrap;
  }
  .sign__divider {
    position: absolute;
    left: 53px;
    top: 166px;
    width: 690px;
    height: 24px;
  }
  .sign__rule {
    position: absolute;
    top: 11px;
    height: 2px;
    width: 300px;
    background: var(--sign-text);
  }
  .sign__rule--left { left: 0; }
  .sign__rule--right { right: 0; }
  .sign__ornament {
    position: absolute;
    left: 310px;
    top: -26px;
    width: 68px;
    height: 74px;
    background: var(--sign-text);
    opacity: 0.55;
    border-radius: 6px;
  }
  .sign__tagline {
    position: absolute;
    left: 0;
    top: 222px;
    width: 100%;
    text-align: center;
    font-size: 60px;
    line-height: 1;
    white-space: nowrap;
  }
  .sign__location {
    position: absolute;
    left: 0;
    top: 310px;
    width: 790px;
    text-align: center;
    font-size: 44px;
    line-height: 1;
    white-space: nowrap;
  }
</style>
</head>
<body>
  <main class="canvas">
    <div class="mountain-crest" role="img" aria-label="Snow-capped mountain range silhouette rising above the sign"></div>
    <section class="sign">
      <h1 class="sign__title">217 MARLOW</h1>
      <div class="sign__divider">
        <span class="sign__rule sign__rule--left"></span>
        <span class="sign__ornament" role="img" aria-label="Decorative floral ornament"></span>
        <span class="sign__rule sign__rule--right"></span>
      </div>
      <p class="sign__tagline">LIVING, WITH INTENT</p>
      <p class="sign__location">Larchmere, Valley Coast</p>
    </section>
  </main>
</body>
</html>
```